'Little Lantern' promotional brochure

We have designed a 6 week program to educate impending first-time parents about the things they need to know to survive the first 6 months. Sessions delivered by general practitioner/family doctor, dietician, physiotherapist, speech pathologist and psychologist. Our promotional blurb is: 'A comprehensive education program for first-time parents-to-be, delivered over 6 weeks by health professionals in your community, about everything you need to know to look after your baby (and yourself!) in the first 6 months'. I now want to put together a promotional brochure to be distributed to those couples who express an interest which will provide further details of what will be delivered in the course.
Updates
In terms of layout, I envisaged a double sided A4 size, foldable into 3 sections, but very happy to be guided on this.
Target Market(s)
To appeal to a young, well educated demographic. First time parents couples.
Industry/Entity Type
Medical
Font styles to use
Other font styles liked:
- Playfair Display
Requirements
Must have
- Playfair display font to be consistent with our logo (attached). Logo also included please. Some consistency with colours of logo please.
Nice to have
- I am a doctor, and have no creative genes! But prefer a clean and professional appearance overall. Not too cluttered in overall appearance.
Should not have
- No cheesy pictures of babies.

```html
<!DOCTYPE html>
<html lang="en">
<head>
<meta charset="utf-8">
<title>Little Lantern – Program Brochure</title>
<link rel="stylesheet" href="https://fonts.googleapis.com/css2?family=Playfair+Display:wght@700&family=Arimo:wght@400&display=swap">
<style>
:root{
  --green:#5bb543;
  --mint-top:#e4f1dd;
  --mint-bottom:#f4f8f2;
  --grey-dark:#6f6f6f;
  --grey-mid:#8f8f8f;
  --grey-soft:#c4c4c4;
  --grey-panel:#e3e3e3;
  --badge-light:#f3f7f0;
  --ink:#2b2b2b;
  --ink-soft:#3a3a3a;
  --white:#ffffff;
  --page:#f1f1f1;
}
*{box-sizing:border-box;margin:0;padding:0}
html,body{width:1200px;height:1200px;overflow:hidden;background:var(--page)}
body{position:relative;font-family:"Arimo",Arial,sans-serif;color:var(--ink)}
.brochure{position:absolute;left:30px;top:184px;width:1140px;height:832px;display:flex;box-shadow:0 6px 22px rgba(0,0,0,.12)}
.panel{position:relative;width:380px;height:100%;overflow:hidden}
.panel--mum,.panel--baby{background:linear-gradient(180deg,var(--mint-top) 0%,var(--mint-bottom) 70%,#fafafa 100%)}
.panel--middle{background:var(--grey-panel)}
.deco{position:absolute;left:0;top:0;width:380px}

.week-badge{position:absolute;top:0;width:180px;height:88px}
.week-badge svg{position:absolute;left:0;top:0;width:180px;height:88px}
.week-title{position:relative;display:block;text-align:center;padding-top:12px;font-family:"Playfair Display",Georgia,serif;font-weight:700;font-size:24px;line-height:30px;font-variant-numeric:lining-nums;color:var(--white)}
.week-badge--light .week-title{color:var(--green)}

.intro{position:absolute;left:24px;right:22px;top:112px;font-size:15.5px;line-height:20px}
.intro .doctor{color:var(--green)}
.topics{list-style:none;margin-top:2px}
.topics li{position:relative;padding-left:16px;line-height:22px}
.topics li::before{content:"";position:absolute;left:2px;top:6px;border-left:8px solid var(--green);border-top:5px solid transparent;border-bottom:5px solid transparent}

.week-two{position:absolute;left:0;top:0;width:380px;height:392px;background:var(--green)}
.week-three{position:absolute;left:0;top:392px;width:380px;height:440px;background:linear-gradient(180deg,#d4d4d4 0%,#ebebeb 60%,#f2f2f2 100%)}
.session{position:absolute;left:22px;right:20px;font-size:14.5px;line-height:18.5px}
.session p{margin-bottom:12px}
.session-label{font-family:"Playfair Display",Georgia,serif;font-weight:700;font-size:16px;font-variant-numeric:lining-nums}
.week-two .session{top:100px;color:var(--white)}
.week-two .session-label{color:var(--ink)}
.week-three .session{top:108px;color:var(--ink-soft)}
.week-three .session-label{color:var(--green)}

.photo{position:absolute}
.photo--diamond{transform:rotate(45deg);border:7px solid var(--white);box-shadow:0 3px 10px rgba(0,0,0,.25)}
.photo--injection{left:50px;top:320px;width:230px;height:150px;background:linear-gradient(135deg,#e9eef3 0%,#9fc3e6 45%,#2f6fb4 100%)}
.photo--newborn-hands{left:60px;top:498px;width:240px;height:240px;background:linear-gradient(135deg,#f2d6c8 0%,#e7b9a5 50%,#c99384 100%)}
.photo--crying-newborn{left:205px;top:400px;width:136px;height:136px;border:none;box-shadow:none;background:linear-gradient(135deg,#f6eeea 0%,#efc6b8 55%,#d99c8a 100%)}
.photo--mother-baby{left:60px;top:498px;width:230px;height:230px;background:linear-gradient(135deg,#f3ede8 0%,#d9b5a0 50%,#8a6a58 100%)}
</style>
</head>
<body>
<main class="brochure">

  <section class="panel panel--mum">
    <svg class="deco" viewBox="0 0 380 832" style="height:832px" aria-hidden="true">
      <polygon points="0,0 24,0 0,60" fill="#b9b9b9"/>
      <polygon points="200,0 240,0 220,20" fill="#9a9a9a"/>
      <polygon points="240,0 290,0 265,24" fill="#cfcfcf"/>
      <polygon points="285,560 345,500 380,535 380,610" fill="#8f8f8f" opacity=".85"/>
      <polygon points="300,760 340,720 380,760 340,800" fill="#d2e3cb"/>
    </svg>
    <div class="week-badge" style="left:24px">
      <svg viewBox="0 0 180 88" aria-hidden="true"><polygon points="0,0 180,0 90,88" fill="var(--green)"/></svg>
      <h2 class="week-title">Week 1</h2>
    </div>
    <div class="intro">
      <p>GP <span class="doctor">Dr Nadia Hollis</span> will share information for Mum's own health after delivery.</p>
      <p>Topics include:</p>
      <ul class="topics">
        <li>Vaccinations in pregnancy</li>
        <li>Bleeding, bladder and bowel after delivery</li>
        <li>Breastfeeding, engorgement and mastitis</li>
        <li>Bottle feeding</li>
        <li>Post-natal anxiety &amp; depression</li>
        <li>Intimacy and contraception</li>
      </ul>
    </div>
    <div class="photo photo--injection" role="img" aria-label="Photo of gloved hands preparing a vaccination syringe"></div>
    <div class="photo photo--diamond photo--newborn-hands" role="img" aria-label="Photo of a newborn's hand holding a parent's finger"></div>
  </section>

  <section class="panel panel--middle">
    <div class="week-two">
      <svg class="deco" viewBox="0 0 380 392" style="height:392px" aria-hidden="true">
        <polygon points="0,0 24,0 0,70" fill="#a9a9a9"/>
        <polygon points="0,80 30,50 60,80 30,110" fill="#c3c3c3" opacity=".7"/>
        <polygon points="204,0 240,0 222,18" fill="#9b9b9b"/>
      </svg>
      <div class="week-badge week-badge--light" style="left:24px">
        <svg viewBox="0 0 180 88" aria-hidden="true"><polygon points="0,0 180,0 90,88" fill="var(--badge-light)"/></svg>
        <h2 class="week-title">Week 2</h2>
      </div>
      <div class="session">
        <p><span class="session-label">Session 1</span> – Clinical Psychologist Dr Maren Tuckwell will discuss changes in relationships as couples becomes parents, gender roles in parenting and post-natal depression.</p>
        <p><span class="session-label">Session 2</span> – Physiotherapist Sofia Larkin will present advice for Mums regarding exercise during and after pregnancy, looking after the pelvic floor during and after pregnancy, and abdominal muscle separation management. She will also provide advice for promoting babies' neck strength and minimising the risk of flat spots on the head and encouraging gross motor skills in the first 6 months.</p>
      </div>
    </div>
    <div class="week-three">
      <svg class="deco" viewBox="0 0 380 440" style="height:440px" aria-hidden="true">
        <polygon points="0,0 24,0 0,50" fill="var(--green)"/>
        <polygon points="190,0 290,0 240,48" fill="#b5b5b5"/>
        <polygon points="260,0 380,0 380,20 330,60" fill="#cfcfcf"/>
      </svg>
      <div class="week-badge" style="left:24px">
        <svg viewBox="0 0 180 88" aria-hidden="true"><polygon points="0,0 180,0 90,88" fill="var(--grey-dark)"/></svg>
        <h2 class="week-title">Week 3</h2>
      </div>
      <div class="session">
        <p><span class="session-label">Session 1</span> – Dietician Ruth Calder provides advice for Mums regarding healthy eating during pregnancy and lactation, normal weight gain during pregnancy and realistic weight loss after. She will also discuss the evidence regarding breastfeeding VS bottle-feeding, normal infant weight gain and introducing solids (including those with potential for allergy).</p>
        <p><span class="session-label">Session 2</span> – Paediatric Speech Pathologist Tessa Morrow will share information about latching and breast-feeding troubles &amp; tongue tie, advice about dummies and finger-sucking, introducing solids &amp; feeding (including 'pouch' food), encouraging language development and current evidence about electronic devices impacting language development.</p>
      </div>
    </div>
  </section>

  <section class="panel panel--baby">
    <svg class="deco" viewBox="0 0 380 832" style="height:832px" aria-hidden="true">
      <polygon points="0,0 24,0 0,80" fill="#a9a9a9"/>
      <polygon points="200,0 240,0 220,20" fill="#9a9a9a"/>
      <polygon points="240,0 300,0 270,30" fill="#d4d4d4"/>
      <polygon points="300,420 380,340 380,600 320,540" fill="#d5e4cf"/>
      <polygon points="270,600 330,540 380,590 380,650 330,700" fill="#8f8f8f"/>
      <polygon points="40,790 80,750 120,790 80,830" fill="#d2e3cb"/>
    </svg>
    <div class="week-badge" style="left:24px">
      <svg viewBox="0 0 180 88" aria-hidden="true"><polygon points="0,0 180,0 90,88" fill="var(--green)"/></svg>
      <h2 class="week-title">Week 4</h2>
    </div>
    <div class="intro">
      <p>GP <span class="doctor">Dr Nadia Hollis</span> will share advice about your babies' health in the first 6 months, including:</p>
      <ul class="topics">
        <li>Skin of newborns</li>
        <li>Sleeping</li>
        <li>Crying</li>
        <li>Immunisations</li>
        <li>Fever and infections</li>
        <li>Diarrhoea and constipation</li>
        <li>Teething</li>
        <li>Understanding a baby's signals</li>
      </ul>
    </div>
    <div class="photo photo--diamond photo--crying-newborn" role="img" aria-label="Photo of a crying newborn baby"></div>
    <div class="photo photo--diamond photo--mother-baby" role="img" aria-label="Photo of a mother cuddling her newborn"></div>
  </section>

</main>
</body>
</html>
```